Corvel Capital LLC

Need Professional Business cards for New Investment Fund

Target Market(s)

High Quality investors

Industry/Entity Type

Financial

Contact Information for Business Card

Phone Number +1 555 284 6190
Name Lukas Varenko
Title Fund Manager
email lv@FundCorvel.com
Website www.FundCorvel.com

Colors

Designer to choose colors to be used in the design.

Requirements
Must have
• Must have our Logo and all of the above. Must be made so lettering and loge can be raised

```html
<!DOCTYPE html>
<html lang="en">
<head>
<meta charset="utf-8">
<title>Quorvane — Business Cards</title>
<link href="https://fonts.googleapis.com/css2?family=Questrial&display=swap" rel="stylesheet">
<style>
  :root {
    --backdrop: #d2d2cc;
    --card: #333333;
    --accent: #22e012;
    --ink: #ffffff;
    --muted: #e6e6e6;
  }
  * { box-sizing: border-box; margin: 0; padding: 0; }
  html, body {
    width: 1200px;
    height: 801px;
    overflow: hidden;
    background: var(--backdrop);
    font-family: "Questrial", "Century Gothic", sans-serif;
  }
  .sheet {
    width: 1200px;
    height: 801px;
    display: flex;
    align-items: center;
    justify-content: center;
    gap: 40px;
  }
  .card {
    width: 540px;
    height: 309px;
    background: var(--card);
    border-bottom: 5px solid var(--accent);
    position: relative;
    box-shadow: 0 12px 28px rgba(0, 0, 0, 0.25);
  }
  .wordmark {
    color: var(--ink);
    font-size: 26px;
    letter-spacing: 3px;
    display: flex;
    align-items: center;
    gap: 10px;
    white-space: nowrap;
  }
  .wordmark .mark-dot {
    width: 12px;
    height: 12px;
    background: var(--accent);
    flex: none;
  }
  .card-front .wordmark {
    position: absolute;
    left: 36px;
    top: 50%;
    transform: translateY(-50%);
  }
  .divider {
    position: absolute;
    left: 282px;
    top: 78px;
    width: 1px;
    height: 150px;
    background: var(--accent);
  }
  .details {
    position: absolute;
    left: 308px;
    top: 72px;
  }
  .person-name {
    color: var(--accent);
    font-size: 24px;
    font-weight: 400;
    letter-spacing: 0.3px;
    white-space: nowrap;
  }
  .person-title {
    color: var(--muted);
    font-size: 16px;
    margin-top: 2px;
  }
  .contacts {
    list-style: none;
    margin-top: 20px;
  }
  .contacts li {
    color: var(--muted);
    font-size: 15px;
    display: flex;
    align-items: center;
    gap: 10px;
    line-height: 27px;
    white-space: nowrap;
  }
  .contacts svg {
    width: 13px;
    height: 13px;
    flex: none;
    stroke: var(--accent);
    fill: none;
    stroke-width: 1.6;
  }
  .contacts .highlight { color: var(--accent); }
  .card-back {
    display: flex;
    align-items: center;
    justify-content: center;
  }
  .card-back .wordmark { font-size: 36px; letter-spacing: 4px; }
</style>
</head>
<body>
<main class="sheet">
  <section class="card card-front" aria-label="Business card front">
    <div class="wordmark"><span class="mark-dot"></span><span>QUORVANE</span></div>
    <div class="divider"></div>
    <div class="details">
      <h1 class="person-name">Lukas Varenko</h1>
      <p class="person-title">Fund Manager</p>
      <ul class="contacts">
        <li>
          <svg viewBox="0 0 14 14" aria-hidden="true"><path d="M3 1.5 L5 1.5 L6 4.5 L4.5 5.5 Q5.5 8.5 8.5 9.5 L9.5 8 L12.5 9 L12.5 11 Q12.5 12.5 11 12.5 Q2 12 1.5 3 Q1.5 1.5 3 1.5 Z"/></svg>
          <span>+1 555 284 6190</span>
        </li>
        <li>
          <svg viewBox="0 0 14 14" aria-hidden="true"><rect x="1.5" y="3" width="11" height="8"/><path d="M1.5 3 L7 7.5 L12.5 3"/></svg>
          <span>lv@FundCorvel.com</span>
        </li>
        <li>
          <svg viewBox="0 0 14 14" aria-hidden="true"><circle cx="7" cy="7" r="5.5"/><ellipse cx="7" cy="7" rx="2.4" ry="5.5"/><path d="M1.5 7 H12.5"/></svg>
          <span>www.<span class="highlight">FundCorvel</span>.com</span>
        </li>
      </ul>
    </div>
  </section>
  <section class="card card-back" aria-label="Business card back">
    <div class="wordmark"><span class="mark-dot"></span><span>QUORVANE</span></div>
  </section>
</main>
</body>
</html>
```